Broschüre für Personaldienstleister
Zielgruppe
Wir sind ein Personaldienstleister und vermitteln ausländisches medizinisches Fachpersonal an deutsche Einrichtungen. Unsere Zielgruppe sind Krankenhäuser, Pflegeheime, Ärztehäuser, Praxen, Labore und weitere medizinische Institutionen.
Aufgabenstellung
Wir haben eine Infobroschüre sowie eine PowerPoint Präsentation bereits mit einem groben Design erstellt. Texte und Beispielbilder (Stockmaterial) sind ebenfalls vorhanden, gerne wünschen wir uns auch Eigeninitiative bei der Wahl der Bilder passend zum neuen Design.
Wir wünschen uns ein Redesign mit einem kreativen, einzigartigen Design. Zudem ist uns wichtig, dass unsere Infografiken qualitativ und hochwertig gestaltet werden.
Dieses Projekt ist mit zukünftigen Folgeprojekten verbunden, da wir weitere Präsentationen und Broschüren für andere Zielgruppen benötigen.

```html
<!DOCTYPE html>
<html lang="de">
<head>
<meta charset="utf-8">
<title>Broschüre – Fachkräftevermittlung</title>
<link href="https://fonts.googleapis.com/css2?family=Roboto+Condensed:wght@500;700&family=Roboto:wght@400;500&display=swap" rel="stylesheet">
<style>
  :root{
    --petrol:#1c3f45;
    --green:#3a8570;
    --mint:#cde6dd;
    --grey:#c9c9c9;
    --text:#4a4a4a;
    --white:#ffffff;
  }
  *{margin:0;padding:0;box-sizing:border-box}
  html,body{width:1200px;height:843px;overflow:hidden;background:#fff}
  body{position:relative;font-family:"Roboto",Arial,sans-serif;color:var(--text)}
  .page-left{position:absolute;left:0;top:0;width:600px;height:843px;background:var(--white)}
  .page-divider{position:absolute;left:600px;top:0;width:3px;height:843px;background:#d0d0d0}
  .page-right{position:absolute;left:608px;top:6px;width:589px;height:833px;background:var(--petrol);overflow:hidden}

  .headline{position:absolute;left:0;width:600px;top:50px;text-align:center;font-family:"Roboto Condensed",Arial,sans-serif;font-weight:700;font-size:28px;color:var(--petrol)}
  .steps-graphic{position:absolute;left:0;top:0}
  .step-text{position:absolute;width:176px;font-size:8.6px;line-height:10.6px;text-align:justify}
  .step-text h3{font-family:"Roboto Condensed",Arial,sans-serif;font-weight:500;font-size:9.2px;color:var(--petrol);text-align:left}
  .step-text.left{left:24px}
  .step-text.right{left:406px;width:170px}

  .first-day{position:absolute;left:24px;top:711px;width:550px}
  .first-day h2{font-family:"Roboto Condensed",Arial,sans-serif;font-weight:500;font-size:18px;color:var(--petrol);margin-bottom:8px}
  .first-day p{font-size:9.8px;line-height:12px;text-align:justify}

  .contact-bar{position:absolute;left:6px;top:813px;width:588px;height:25px;background:var(--petrol);color:var(--white);font-size:10px}
  .contact-bar span{position:absolute;top:6px;transform:translateX(-50%)}

  .talent-title{position:absolute;left:0;width:589px;top:34px;text-align:center;font-family:"Roboto Condensed",Arial,sans-serif;font-weight:700;font-size:28px;color:var(--white)}
  .talent-list{position:absolute;left:10px;width:569px;top:80px;text-align:center;font-size:13.6px;line-height:16.6px;color:var(--white)}
  .talent-more{position:absolute;left:0;width:589px;top:191px;text-align:center;font-size:13.6px;color:var(--white)}
  .talent-photo{position:absolute;left:60px;top:320px;width:450px;height:513px;border-radius:200px 200px 0 0;background:linear-gradient(180deg,#7a4a32 0%,#d9a98e 30%,#3f86c9 58%,#2f73b8 100%);opacity:.9}
</style>
</head>
<body>
<section class="page-left">
  <h1 class="headline">In 6 Schritten zu Ihrer neuen Fachkraft</h1>

  <svg class="steps-graphic" width="600" height="700" viewBox="0 0 600 700">
    <rect x="298" y="190" width="10" height="450" fill="var(--grey)"/>
    <!-- Step 1 -->
    <rect x="228" y="154" width="241" height="12" fill="var(--green)"/>
    <circle cx="228" cy="160" r="16" fill="var(--petrol)"/>
    <circle cx="469" cy="160" r="23" fill="#fff" stroke="var(--petrol)" stroke-width="6"/>
    <text x="469" y="168" text-anchor="middle" font-family="Roboto Condensed" font-weight="700" font-size="21" fill="var(--petrol)">1</text>
    <circle cx="303" cy="160" r="38" fill="#fff" stroke="var(--petrol)" stroke-width="9"/>
    <g fill="none" stroke="var(--petrol)" stroke-width="1.6"><rect x="289" y="144" width="26" height="31" rx="2"/><circle cx="302" cy="155" r="5"/><path d="M293 168q9-9 18 0M295 172h14M315 149h3v6h-3M315 158h3v6h-3"/></g>
    <!-- Step 2 -->
    <rect x="136" y="250" width="241" height="12" fill="var(--petrol)"/>
    <circle cx="377" cy="256" r="16" fill="var(--green)"/>
    <circle cx="136" cy="256" r="23" fill="#fff" stroke="var(--green)" stroke-width="6"/>
    <text x="136" y="264" text-anchor="middle" font-family="Roboto Condensed" font-weight="700" font-size="21" fill="var(--petrol)">2</text>
    <circle cx="303" cy="256" r="38" fill="#fff" stroke="var(--green)" stroke-width="9"/>
    <g fill="var(--petrol)"><path d="M285 236h18l10 10v12l-8 8v8h-23z"/><path d="M310 262l10-10 5 5-10 10h-5z"/></g>
    <g stroke="#fff" stroke-width="2.2"><path d="M289 248h10M289 255h16M289 262h12"/></g>
    <!-- Step 3 -->
    <rect x="228" y="345" width="241" height="12" fill="var(--petrol)"/>
    <circle cx="228" cy="351" r="16" fill="var(--mint)"/>
    <circle cx="469" cy="351" r="23" fill="#fff" stroke="var(--mint)" stroke-width="6"/>
    <text x="469" y="359" text-anchor="middle" font-family="Roboto Condensed" font-weight="700" font-size="21" fill="var(--petrol)">3</text>
    <circle cx="303" cy="351" r="38" fill="#fff" stroke="var(--mint)" stroke-width="9"/>
    <g fill="none" stroke="var(--petrol)" stroke-width="1.6"><path d="M300 336l3 3 5-6"/><circle cx="303" cy="347" r="4"/><circle cx="293" cy="353" r="4"/><circle cx="313" cy="353" r="4"/><path d="M285 368q0-9 8-9q8 0 8 9zM305 368q0-9 8-9q8 0 8 9zM296 362q7-10 14 0"/></g>
    <!-- Step 4 -->
    <rect x="136" y="440" width="241" height="12" fill="var(--green)"/>
    <circle cx="377" cy="446" r="16" fill="var(--petrol)"/>
    <circle cx="136" cy="446" r="23" fill="#fff" stroke="var(--petrol)" stroke-width="6"/>
    <text x="136" y="454" text-anchor="middle" font-family="Roboto Condensed" font-weight="700" font-size="21" fill="var(--petrol)">4</text>
    <circle cx="303" cy="446" r="38" fill="#fff" stroke="var(--petrol)" stroke-width="9"/>
    <g fill="none" stroke="var(--petrol)" stroke-width="1.5"><rect x="295" y="426" width="10" height="6" rx="1"/><circle cx="291" cy="439" r="3.5"/><circle cx="315" cy="439" r="3.5"/><path d="M283 466v-16h8l4 8M323 466v-16h-8l-4 8M293 452h20M297 452v14M309 452v14M305 446h6"/></g>
    <!-- Step 5 -->
    <rect x="228" y="536" width="241" height="12" fill="var(--mint)"/>
    <circle cx="228" cy="542" r="16" fill="var(--green)"/>
    <circle cx="469" cy="542" r="23" fill="#fff" stroke="var(--green)" stroke-width="6"/>
    <text x="469" y="550" text-anchor="middle" font-family="Roboto Condensed" font-weight="700" font-size="21" fill="var(--petrol)">5</text>
    <circle cx="303" cy="542" r="38" fill="#fff" stroke="var(--green)" stroke-width="9"/>
    <g fill="none" stroke="var(--petrol)" stroke-width="1.2"><circle cx="288" cy="526" r="2.5"/><circle cx="318" cy="526" r="2.5"/><circle cx="288" cy="556" r="2.5"/><circle cx="318" cy="556" r="2.5"/><circle cx="303" cy="538" r="4"/><path d="M296 550q7-8 14 0M294 527h8M306 527h8M294 557h8M306 557h8M288 533v14M318 533v14"/></g>
    <!-- Step 6 -->
    <rect x="136" y="638" width="241" height="12" fill="var(--green)"/>
    <circle cx="377" cy="644" r="16" fill="var(--petrol)"/>
    <circle cx="136" cy="644" r="23" fill="#fff" stroke="var(--petrol)" stroke-width="6"/>
    <text x="136" y="652" text-anchor="middle" font-family="Roboto Condensed" font-weight="700" font-size="21" fill="var(--petrol)">6</text>
    <circle cx="303" cy="644" r="38" fill="#fff" stroke="var(--petrol)" stroke-width="9"/>
    <g fill="var(--petrol)"><path d="M277 634l8-4 14 2 10-4 8 2 9 4v14l-6 2-14 12-6-4-8-2-15-10z"/></g>
    <g fill="none" stroke="#fff" stroke-width="1.6"><path d="M296 637l8-3 10 6M296 650l5 4M300 646l6 5M304 642l6 5"/></g>
  </svg>

  <div class="step-text left" style="top:135px"><h3>Kontaktaufnahme</h3>Sie nehmen Kontakt zu uns auf und teilen uns Ihren Personalbedarf, sowie spezielle Stellenanforderungen mit.</div>
  <div class="step-text right" style="top:236px"><h3>Vertragsmodalitäten</h3>Wir setzen uns mit Ihnen zusammen, besprechen die Einzelheiten und klären die Rahmenbedingungen, individuell auf Sie zugeschnitten.</div>
  <div class="step-text left" style="top:325px"><h3>Kandidatenvorauswahl</h3>Wir lassen Ihnen vorab übersichtliche CV’s potenzieller Kandidat:innen zukommen und Sie treffen eine Vorauswahl bzw. teilen uns eventuelle Anpassungswünsche mit.</div>
  <div class="step-text right" style="top:425px"><h3>Vorstellungsgespräche</h3>Sie führen die Vorstellungsgespräche mit den Kandidat:innen durch. Unsere Expert:innen begleiten Sie dabei als wichtiges Bindeglied, um bei Missverständnissen und Unklarheiten vorzubeugen.</div>
  <div class="step-text left" style="top:524px"><h3>Finale Personalauswahl</h3>Sie entscheiden sich für Ihre Wunschmitarbeiter:innen - wir stellen Ihnen zusammen mit einer persönlichen Einschätzung zu den jeweiligen Kandidat:innen alle Informationen und Unterlagen in einem übersichtlichen und informativen Bericht zur Verfügung.</div>
  <div class="step-text right" style="top:623px"><h3>Arbeitsvertrag</h3>Nach Klärung aller wichtigen Modalitäten und Besonderheiten unterschreibt der/die Bewerber:in seinen/ihren Arbeitsvertrag.</div>

  <div class="first-day">
    <h2>Erster Arbeitstag</h2>
    <p>Wir begleiten und betreuen unsere Kandidat:innen über den kompletten Auswahlprozess hinweg bis zum Ende ihrer Probezeit. Nicht selten können wir auch nach der erfolgreichen Vermittlung noch wertvolle Klärungs- und Motivationsarbeit leisten. Außerdem übernehmen wir sowohl Abschlussgespräche, als auch die gesamte Korrespondenz mit allen Bewerber:innen, die am Auswahlverfahren beteiligt waren.</p>
  </div>

  <footer class="contact-bar">
    <span style="left:110px">+49 000 118 27 350</span>
    <span style="left:298px">hr@velmora-care.com</span>
    <span style="left:475px">www.velmora-care.com</span>
  </footer>
</section>

<div class="page-divider"></div>

<section class="page-right">
  <h2 class="talent-title">Unser Talentpool</h2>
  <p class="talent-list">Gesundheits- und Krankenpfleger:in I Pflegefachmann /-frau I Pflegefachassistent:in I<br>Altenpfleger:in I Arzt/Ärztin I Hebamme I Anästhesietechnische:r Assistent:in (ATA) I<br>Operationstechnische:r Assistent:in (OTA) I Medizinisch-technische:r<br>Laborassistent:in (MTLA) I Medizinisch-technische:r Radiologieassistentin (MTRA) I<br>Pflegehilfskräfte I Pflegefachassistent:in I Notfallsanitäter:in I Rettungssanitäter:in I<br>Physiotherapeut:innen I</p>
  <p class="talent-more">… und viele weitere medizinische Berufe.</p>
  <div class="talent-photo" role="img" aria-label="Foto: lächelnde Pflegekraft in blauer Berufskleidung, die mit beiden Händen auf die Berufsliste zeigt"></div>
</section>
</body>
</html>
```